Brenvik Systems PowerPoint Template

Project Title: Professional & Functional PowerPoint Template (.potx) – Brenvik Systems Rebrand

Project Overview:
Brenvik Systems has recently undergone a complete rebranding, including a new logo, website, and visual identity. We need a professional, high-end PowerPoint Template (.potx) that reflects our new look while being highly functional for everyday use.

We previously had a design created, but it was built incorrectly (static images, oversized file, no Master Slides). The goal of this project is to take our new aesthetic and build a "workable" template where layouts are controlled by Master Slides and text is easily editable.

Style & Brand Direction:
The template must be an extension of our new website: https://www.brenvik-systems.example/

Aesthetic: Modern, clean, high-tech, and "Industrial Tech."

Color Palette: Please pull the primary blues, greys, and accent colors directly from the website.

Imagery/Graphics: Use clean lines and subtle tech-inspired gradients. Avoid "clutter."

Tone: Innovative, precise, and professional.

Technical Requirements (Crucial)
Format: Must be delivered as a PowerPoint Template file (** .potx **).

Functionality: All layouts must be built using Slide Masters. Users should be able to click "New Slide" and choose from specific layouts.

Native Elements: Do NOT use full-page background images for text areas. Bullet points must use native PowerPoint list functionality (not individual text boxes).

File Size: The template must be optimized and lightweight.

Fonts: Use standard professional fonts or provide the specific web-safe equivalent used on our site (e.g., Montserrat, Open Sans, etc.).

Required Slide Layouts
Please include a minimum of 10–12 Master layouts, including:
*Title Slide (2-3 variations: Dark and Light)
*Agenda/Table of Contents
*Section Header/Divider Slides
*Standard Text/Bullet Slide
*Two-Column Text Slide
*Image + Text Layouts (Left/Right variations)
*Data/Chart Slide (Styled bar/pie charts that match the brand)
*Process/Timeline Slide (Infographic style)
*Section slide

Attachments Provided
Brand Assets (.zip): Contains our new logo in various formats.

Inspiration/Existing PPT: We have attached the previous design created by our web agency. Note: Use this for visual inspiration ONLY. Do not copy the file structure, as it is technically flawed.

Deliverables
Final .potx file.

All used icons or custom graphics in vector format (if applicable).

Instruction note on any specific fonts used.

Target Market(s)

Internal communication and external (investors, customers)

Industry/Entity Type

Semiconductor, Automotive

Requirements
Must have
• A potx file

```html
<!DOCTYPE html>
<html lang="en">
<head>
<meta charset="utf-8">
<title>Brenvik Systems – Presentation Template Overview</title>
<link href="https://fonts.googleapis.com/css2?family=Inter:wght@300;400;600&family=Allura&display=swap" rel="stylesheet">
<style>
:root{
  --page:#8db8f5;
  --blue:#2553f5;
  --blue-deep:#1537c9;
  --navy:#0b1a4a;
  --ink:#0d0d0f;
  --grey:#f1f1f1;
  --line:#d6d9e0;
  --muted:#4a4d55;
  --white:#ffffff;
}
*{box-sizing:border-box;margin:0;padding:0}
html,body{width:859px;height:1200px;overflow:hidden}
body{background:var(--page);font-family:"Inter",Arial,sans-serif;font-weight:300;color:var(--ink);position:relative}
.slide{position:absolute;width:390px;height:220px;overflow:hidden;background:var(--white)}
.abs{position:absolute}
.arrow{position:absolute;display:block}
.lines{white-space:nowrap}
.t-sm{font-size:6px;line-height:1.3;white-space:nowrap}
.rule{border-left:0.8px solid currentColor;padding-left:6px}
.item{white-space:nowrap}
.item h4{font-weight:300;font-size:9.5px;line-height:1.1}
.item p{font-size:7px;line-height:1.25;color:var(--muted)}
.wordmark{font-weight:600;color:var(--white);letter-spacing:.5px;display:flex;align-items:center;gap:6px}
.wordmark .mark{background:var(--white);display:inline-block}
.eyebrow{font-size:8.5px;letter-spacing:2px;text-transform:uppercase;font-weight:300}
.headline{font-weight:300;letter-spacing:-.3px;white-space:nowrap}
.card{position:absolute;padding:6px 7px;white-space:nowrap}
.card h5{font-weight:300;font-size:9.5px;line-height:1.15;margin-bottom:1px}
.card p{font-size:6.6px;line-height:1.32;color:var(--muted)}
.card.filled{background:var(--grey)}
.card.outlined{border:0.8px solid #c9d3f5;background:var(--white)}
</style>
</head>
<body>

<!-- Title slide -->
<section class="slide title-dark" style="left:35px;top:33px;background:linear-gradient(90deg,#050b1e 0%,#0f2a8a 18%,#061033 30%,#1a3ec4 45%,#050b1e 58%,#0a0f1c 100%)">
  <div class="abs" role="img" aria-label="Photograph of vertical blue light streaks" style="inset:0;background:linear-gradient(180deg,rgba(0,0,0,.15),rgba(0,0,0,.55))"></div>
  <div class="abs wordmark" style="left:44px;top:94px;font-size:28px">
    <span class="mark" style="width:22px;height:22px"></span>BRENVIK
  </div>
  <h1 class="abs headline" style="left:216px;top:58px;font-size:25px;line-height:1.15;color:var(--white)">Enlightened<br>Engineering</h1>
  <p class="abs rule lines" style="left:218px;top:133px;font-size:9.5px;line-height:1.3;color:var(--white)">Unlocking the power of<br>light for cleaner, smarter,<br>more scalable production.</p>
  <svg class="arrow" style="left:344px;top:39px" width="14" height="14" viewBox="0 0 14 14"><rect width="14" height="14" fill="var(--blue)"/><path d="M4 10L10 4M5.5 4H10V8.5" stroke="#fff" stroke-width="1.2" fill="none"/></svg>
  <svg class="arrow" style="left:187px;top:183px" width="14" height="14" viewBox="0 0 14 14"><rect width="14" height="14" fill="var(--blue)"/><path d="M4 10L10 4M5.5 4H10V8.5" stroke="#fff" stroke-width="1.2" fill="none"/></svg>
</section>

<!-- Agenda -->
<section class="slide agenda" style="left:434px;top:33px">
  <svg class="abs" style="left:0;top:0" width="390" height="220">
    <path d="M0 69H253A41 41 0 0 1 253 151H0" stroke="var(--line)" stroke-width=".8" fill="none"/>
    <g fill="#fff" stroke="var(--line)" stroke-width=".8">
      <circle cx="44" cy="69" r="3"/><circle cx="122" cy="69" r="3"/><circle cx="203" cy="69" r="3"/>
      <circle cx="44" cy="151" r="3"/><circle cx="122" cy="151" r="3"/><circle cx="203" cy="151" r="3"/>
      <circle cx="272" cy="86" r="3"/><circle cx="272" cy="134" r="3"/>
    </g>
  </svg>
  <div class="abs item" style="left:39px;top:31px"><h4>Lorem Ipsum</h4><p>Lorem ipsum dolor<br>sit amet</p></div>
  <div class="abs item" style="left:117px;top:31px"><h4>Lorem Ipsum</h4><p>Lorem ipsum dolor<br>sit amet</p></div>
  <div class="abs item" style="left:198px;top:31px"><h4>Lorem Ipsum</h4><p>Lorem ipsum dolor<br>sit amet</p></div>
  <div class="abs item" style="left:287px;top:64px"><h4>Lorem Ipsum</h4><p>Lorem ipsum dolor<br>sit amet</p></div>
  <div class="abs item" style="left:287px;top:113px"><h4>Lorem Ipsum</h4><p>Lorem ipsum dolor<br>sit amet</p></div>
  <div class="abs item" style="left:39px;top:164px"><h4>Lorem Ipsum</h4><p>Lorem ipsum dolor<br>sit amet</p></div>
  <div class="abs item" style="left:117px;top:164px"><h4>Lorem Ipsum</h4><p>Lorem ipsum dolor<br>sit amet</p></div>
  <div class="abs item" style="left:198px;top:164px"><h4>Lorem Ipsum</h4><p>Lorem ipsum dolor<br>sit amet</p></div>
  <h2 class="abs headline" style="left:169px;top:90px;font-size:25px">Agenda</h2>
  <svg class="arrow" style="left:146px;top:119px" width="19" height="19" viewBox="0 0 14 14"><rect width="14" height="14" fill="var(--ink)"/><path d="M4 10L10 4M5.5 4H10V8.5" stroke="#fff" stroke-width="1.1" fill="none"/></svg>
</section>

<!-- Text + image -->
<section class="slide text-image" style="left:35px;top:263px">
  <h3 class="abs lines" style="left:25px;top:57px;font-weight:300;font-size:11.3px;line-height:1.27">For industries driving tech<br>forward, Brenvik is the most<br>advanced laser-based<br>manufacturing partner</h3>
  <p class="abs t-sm rule" style="left:25px;top:124px;color:var(--muted)">Lorem ipsum dolor sit amet, consectetur<br>adipiscing elit, sed do eiusmod tempor incididunt<br>ut labore et dolore magna aliqua. Quis ipsum<br>suspendisse ultrices gravida. Risus commodo<br>viverra maecenas accumsan lacus vel facilisis.</p>
  <svg class="arrow" style="left:172px;top:28px" width="14" height="14" viewBox="0 0 14 14"><rect width="14" height="14" fill="var(--blue)"/><path d="M4 10L10 4M5.5 4H10V8.5" stroke="#fff" stroke-width="1.2" fill="none"/></svg>
  <div class="abs" role="img" aria-label="Photograph of a laser cutting head throwing orange sparks" style="left:182px;top:9px;width:199px;height:201px;background:radial-gradient(circle at 55% 48%,#ffb347 0%,#b5591a 18%,#3a2a20 45%,#15171c 80%)"></div>
  <ul class="abs lines" style="left:197px;top:124px;list-style:none;color:var(--white);font-size:6.3px;line-height:1.3">
    <li style="margin-bottom:3px;padding-left:10px;position:relative"><span class="abs" style="left:0">↗</span>Lorem ipsum dolor sit amet, consectetur<br>adipiscing elit, sed do eiusmod tempor<br>incididunt ut labore et dolore magna aliqua</li>
    <li style="margin-bottom:3px;padding-left:10px;position:relative"><span class="abs" style="left:0">↗</span>Quis ipsum suspendisse ultrices gravida.</li>
    <li style="padding-left:10px;position:relative"><span class="abs" style="left:0">↗</span>Risus commodo viverra maecenas accumsan<br>lacus vel facilisis.</li>
  </ul>
  <span class="abs" style="left:352px;top:181px;width:19px;height:19px;background:var(--blue)"></span>
</section>

<!-- Section divider -->
<section class="slide section-divider" style="left:434px;top:263px">
  <div class="abs" style="left:0;top:0;width:390px;height:105px;background:var(--blue)"></div>
  <h2 class="abs headline" style="left:29px;top:42px;font-size:21px;line-height:1.05;color:var(--white)">Section<br>Divider</h2>
  <svg class="arrow" style="left:104px;top:31px" width="14" height="14" viewBox="0 0 14 14"><rect width="14" height="14" fill="var(--ink)"/><path d="M4 10L10 4M5.5 4H10V8.5" stroke="#fff" stroke-width="1.2" fill="none"/></svg>
  <p class="abs t-sm rule" style="left:213px;top:61px;color:var(--white)">Lorem ipsum dolor sit amet, consectetur<br>adipiscing elit, sed do eiusmod tempor incididunt<br>ut labore et dolore magna aliqua.</p>
  <p class="abs t-sm" style="left:29px;top:126px;color:var(--muted)">Lorem ipsum dolor sit amet, consectetur<br>adipiscing elit, sed do eiusmod tempor incididunt<br>ut labore et dolore magna aliqua. Quis ipsum<br>suspendisse ultrices gravida. Risus commodo<br>viverra maecenas accumsan lacus vel facilisis.</p>
  <p class="abs t-sm" style="left:29px;top:172px;color:var(--ink)">Lorem ipsum dolor sit amet, consectetur<br>adipiscing elit, sed do eiusmod tempor.</p>
  <div class="abs" role="img" aria-label="Photograph of a rocket engine in an industrial hangar" style="left:181px;top:114px;width:200px;height:96px;background:linear-gradient(120deg,#1c2530 0%,#4a5560 40%,#9aa1a8 55%,#5a3f2a 80%,#1a1d22 100%)"></div>
</section>

<!-- Partner with precision -->
<section class="slide features" style="left:35px;top:491px">
  <div class="abs" style="left:138px;top:0;width:15px;height:220px;background:#f4f4f5"></div>
  <h2 class="abs headline" style="left:27px;top:58px;font-size:20px;line-height:1.08">Partner with<br>Precision</h2>
  <svg class="arrow" style="left:127px;top:94px" width="10" height="10" viewBox="0 0 14 14"><rect width="14" height="14" fill="var(--blue)"/><path d="M4 10L10 4M5.5 4H10V8.5" stroke="#fff" stroke-width="1.3" fill="none"/></svg>
  <p class="abs t-sm" style="left:27px;top:111px;color:var(--muted)">Lorem ipsum dolor sit amet, consectetur<br>adipiscing elit, sed do eiusmod tempor<br>incididunt ut labore et dolore magna.</p>
  <p class="abs t-sm" style="left:27px;top:142px;color:var(--muted)">Quis ipsum suspendisse ultrices gravida.<br>Risus commodo viverra maecenas<br>accumsan lacus vel facilisis.</p>
  <div class="card filled" style="left:161px;top:38px;width:100px;height:54px"><h5>Minimize Cost</h5><p>Eliminate expensive tools<br>while reducing labor costs<br>through full automation.</p></div>
  <div class="card outlined" style="left:161px;top:96px;width:100px;height:73px"><h5>Improve Quality</h5><p>Laser-controlled<br>geometry creates ultra-<br>smooth surfaces that<br>enhance device<br>performance</p></div>
  <div class="card outlined" style="left:266px;top:55px;width:101px;height:54px"><h5>Reduce Waste</h5><p>Achieve 2.2-2.3 wafers per<br>mm with 90% kerf loss<br>reduction</p></div>
  <div class="card filled" style="left:266px;top:113px;width:101px;height:61px"><h5>Increase Yields</h5><p>Consistent process<br>prevents stress damage<br>while delivering<br>predictable output</p></div>
  <svg class="arrow" style="left:226px;top:162px" width="19" height="19" viewBox="0 0 14 14"><rect width="14" height="14" fill="var(--ink)"/><path d="M4 10L10 4M5.5 4H10V8.5" stroke="#fff" stroke-width="1.1" fill="none"/></svg>
  <svg class="arrow" style="left:343px;top:49px" width="10" height="10" viewBox="0 0 14 14"><rect width="14" height="14" fill="var(--blue)"/><path d="M4 10L10 4M5.5 4H10V8.5" stroke="#fff" stroke-width="1.3" fill="none"/></svg>
  <span class="abs" style="left:362px;top:8px;width:19px;height:19px;background:#c9cbd0"></span>
</section>

<!-- Bar chart -->
<section class="slide bar-chart" style="left:434px;top:491px">
  <p class="abs eyebrow" style="left:0;width:390px;top:27px;text-align:center">Lorem Ipsum</p>
  <h2 class="abs headline" style="left:0;width:390px;top:37px;text-align:center;font-size:22px">Lorem Ipsum</h2>
  <svg class="abs" style="left:0;top:0" width="390" height="220">
    <g font-family="Inter, sans-serif" font-size="10" font-weight="600" text-anchor="middle">
      <g>
        <rect x="133" y="78" width="12" height="100" rx="6" fill="#e4e6ea"/><rect x="135" y="80" width="8" height="98" rx="4" fill="#cfd2d8"/>
        <rect x="135" y="139" width="8" height="39" fill="#8cc7f0"/>
        <circle cx="139" cy="184" r="12" fill="#fff" stroke="#e4e6ea" stroke-width="2"/><text x="139" y="188" fill="#8cc7f0">A</text>
      </g>
      <g>
        <rect x="166" y="78" width="12" height="100" rx="6" fill="#e4e6ea"/><rect x="168" y="80" width="8" height="98" rx="4" fill="#cfd2d8"/>
        <rect x="168" y="127" width="8" height="51" fill="#2a8fd8"/>
        <circle cx="172" cy="184" r="12" fill="#fff" stroke="#e4e6ea" stroke-width="2"/><text x="172" y="188" fill="#2a8fd8">B</text>
      </g>
      <g>
        <rect x="198" y="78" width="12" height="100" rx="6" fill="#e4e6ea"/><rect x="200" y="80" width="8" height="98" rx="4" fill="#cfd2d8"/>
        <rect x="200" y="109" width="8" height="69" fill="#2c5fc0"/>
        <circle cx="204" cy="184" r="12" fill="#fff" stroke="#e4e6ea" stroke-width="2"/><text x="204" y="188" fill="#2c5fc0">C</text>
      </g>
      <g>
        <rect x="231" y="78" width="12" height="100" rx="6" fill="#e4e6ea"/><rect x="233" y="80" width="8" height="98" rx="4" fill="#cfd2d8"/>
        <rect x="233" y="94" width="8" height="84" fill="#1c2d6b"/>
        <circle cx="237" cy="184" r="12" fill="#fff" stroke="#e4e6ea" stroke-width="2"/><text x="237" y="188" fill="#1c2d6b">D</text>
      </g>
    </g>
  </svg>
  <div class="abs item" style="left:52px;top:77px"><h4>Lorem Ipsum</h4><p>Lorem ipsum dolor<br>sit amet</p></div>
  <div class="abs item" style="left:37px;top:117px"><h4>Lorem Ipsum</h4><p>Lorem ipsum dolor<br>sit amet</p></div>
  <div class="abs item" style="left:52px;top:161px"><h4>Lorem Ipsum</h4><p>Lorem ipsum dolor<br>sit amet</p></div>
  <div class="abs item" style="left:278px;top:77px"><h4>Lorem Ipsum</h4><p>Lorem ipsum dolor<br>sit amet</p></div>
  <div class="abs item" style="left:299px;top:117px"><h4>Lorem Ipsum</h4><p>Lorem ipsum dolor<br>sit amet</p></div>
  <div class="abs item" style="left:278px;top:161px"><h4>Lorem Ipsum</h4><p>Lorem ipsum dolor<br>sit amet</p></div>
</section>

<!-- Timeline -->
<section class="slide timeline" style="left:35px;top:720px;background:var(--ink);color:var(--white)">
  <svg class="arrow" style="left:31px;top:35px" width="18" height="18" viewBox="0 0 14 14"><rect width="14" height="14" fill="#1b1b1e"/><path d="M4 10L10 4M5.5 4H10V8.5" stroke="#fff" stroke-width="1.1" fill="none"/></svg>
  <p class="abs eyebrow" style="left:58px;top:28px;font-size:10px">Lorem Ipsum</p>
  <h2 class="abs headline" style="left:58px;top:38px;font-size:18px">Lorem Ipsum</h2>
  <p class="abs t-sm rule" style="left:185px;top:33px">Lorem ipsum dolor sit amet, consectetur<br>adipiscing elit, sed do eiusmod tempor incididunt<br>ut labore et dolore magna aliqua.</p>
  <svg class="arrow" style="left:347px;top:30px" width="10" height="10" viewBox="0 0 14 14"><rect width="14" height="14" fill="var(--blue)"/><path d="M4 10L10 4M5.5 4H10V8.5" stroke="#fff" stroke-width="1.3" fill="none"/></svg>
  <svg class="abs" style="left:0;top:0" width="390" height="220">
    <line x1="0" y1="136" x2="390" y2="136" stroke="#fff" stroke-width=".7"/>
    <g fill="var(--ink)" stroke="var(--blue)" stroke-width="1">
      <circle cx="69" cy="136" r="4.5"/><circle cx="117" cy="136" r="4.5"/><circle cx="169" cy="136" r="4.5"/>
      <circle cx="220" cy="136" r="4.5"/><circle cx="270" cy="136" r="4.5"/><circle cx="320" cy="136" r="4.5"/>
    </g>
    <g fill="var(--blue)">
      <circle cx="69" cy="136" r="2.3"/><circle cx="117" cy="136" r="2.3"/><circle cx="169" cy="136" r="2.3"/>
      <circle cx="220" cy="136" r="2.3"/><circle cx="270" cy="136" r="2.3"/><circle cx="320" cy="136" r="2.3"/>
    </g>
  </svg>
  <div class="abs item" style="left:29px;top:85px;width:80px;text-align:center"><h4>Lorem Ipsum</h4><p style="color:#ccc">Lorem ipsum dolor<br>sit amet, consectetur<br>adipiscing elit</p></div>
  <div class="abs item" style="left:129px;top:85px;width:80px;text-align:center"><h4>Lorem Ipsum</h4><p style="color:#ccc">Lorem ipsum dolor<br>sit amet, consectetur<br>adipiscing elit</p></div>
  <div class="abs item" style="left:230px;top:85px;width:80px;text-align:center"><h4>Lorem Ipsum</h4><p style="color:#ccc">Lorem ipsum dolor<br>sit amet, consectetur<br>adipiscing elit</p></div>
  <div class="abs item" style="left:77px;top:151px;width:80px;text-align:center"><h4>Lorem Ipsum</h4><p style="color:#ccc">Lorem ipsum dolor<br>sit amet, consectetur<br>adipiscing elit</p></div>
  <div class="abs item" style="left:180px;top:151px;width:80px;text-align:center"><h4>Lorem Ipsum</h4><p style="color:#ccc">Lorem ipsum dolor<br>sit amet, consectetur<br>adipiscing elit</p></div>
  <div class="abs item" style="left:280px;top:151px;width:80px;text-align:center"><h4>Lorem Ipsum</h4><p style="color:#ccc">Lorem ipsum dolor<br>sit amet, consectetur<br>adipiscing elit</p></div>
  <span class="abs" style="left:11px;top:191px;width:19px;height:19px;background:var(--blue)"></span>
</section>

<!-- Donut / pie data -->
<section class="slide pie-data" style="left:434px;top:720px">
  <p class="abs eyebrow" style="left:0;width:390px;top:23px;text-align:center">Lorem Ipsum</p>
  <h2 class="abs headline" style="left:0;width:390px;top:33px;text-align:center;font-size:22px">Lorem Ipsum</h2>
  <div class="card filled" style="left:28px;top:59px;width:77px;height:58px;padding:20px 0 0 21px"><h5 style="font-size:8.5px">Lorem Ipsum</h5><p>Lorem ipsum<br>dolor sit amet</p></div>
  <div class="card outlined" style="left:28px;top:122px;width:77px;height:50px;padding:8px 0 0 21px"><h5 style="font-size:8.5px">Lorem Ipsum</h5><p>Lorem ipsum<br>dolor sit amet</p></div>
  <div class="card outlined" style="left:111px;top:79px;width:77px;height:53px;padding:20px 0 0 6px"><h5 style="font-size:8.5px">Lorem Ipsum</h5><p>Lorem ipsum<br>dolor sit amet</p></div>
  <div class="card filled" style="left:111px;top:140px;width:77px;height:52px;padding:10px 0 0 6px"><h5 style="font-size:8.5px">Lorem Ipsum</h5><p>Lorem ipsum<br>dolor sit amet</p></div>
  <svg class="abs" style="left:0;top:0" width="390" height="220" font-family="Inter, sans-serif" font-weight="600">
    <g stroke-width="4" fill="#fff">
      <circle cx="33" cy="61" r="16" stroke="#eef0f4"/><circle cx="33" cy="61" r="11" stroke="#e6e8ee"/>
      <path d="M33 50A11 11 0 0 0 33 72" stroke="#1c2d6b"/>
      <circle cx="35" cy="170" r="16" stroke="#eef0f4"/><circle cx="35" cy="170" r="11" stroke="#e6e8ee"/>
      <path d="M35 159A11 11 0 1 0 38.5 180.4" stroke="#2a8fd8"/>
      <circle cx="186" cy="84" r="16" stroke="#eef0f4"/><circle cx="186" cy="84" r="11" stroke="#e6e8ee"/>
      <path d="M186 73A11 11 0 1 0 189.5 94.4" stroke="#2a8fd8"/>
      <circle cx="186" cy="190" r="16" stroke="#eef0f4"/><circle cx="186" cy="190" r="11" stroke="#e6e8ee"/>
      <path d="M186 179A11 11 0 1 0 197 190" stroke="#1c2d6b"/>
    </g>
    <g font-size="4.5" fill="#2a8fd8" text-anchor="middle">
      <text x="33" y="62.5">50%</text><text x="35" y="171.5">47%</text><text x="186" y="85.5">47%</text><text x="186" y="191.5">75%</text>
    </g>
    <g>
      <path d="M372 113L372 55A58 58 0 0 0 350 59Z" fill="#123a7a"/>
      <path d="M372 113L345 73A48 48 0 0 0 326 99Z" fill="#3fd0f0"/>
      <path d="M372 113L320 99A54 54 0 0 0 320 127Z" fill="#1a8fd0"/>
      <path d="M372 113L334 124A40 40 0 0 0 342 140Z" fill="#0f69b8"/>
      <path d="M372 113L338 151A52 52 0 0 0 372 167Z" fill="#19a6e6"/>
      <circle cx="372" cy="113" r="13" fill="#fff"/>
      <path d="M372 103A10 10 0 0 0 372 123Z" fill="#123a7a"/>
    </g>
  </svg>
  <div class="abs item" style="left:306px;top:22px"><h4 style="font-size:8.5px">Lorem Ipsum</h4><p style="font-size:6.5px">Lorem ipsum<br>dolor sit amet</p></div>
  <div class="abs item" style="left:270px;top:58px"><h4 style="font-size:8.5px">Lorem Ipsum</h4><p style="font-size:6.5px">Lorem ipsum<br>dolor sit amet</p></div>
  <div class="abs item" style="left:252px;top:99px"><h4 style="font-size:8.5px">Lorem Ipsum</h4><p style="font-size:6.5px">Lorem ipsum<br>dolor sit amet</p></div>
  <div class="abs item" style="left:275px;top:138px"><h4 style="font-size:8.5px">Lorem Ipsum</h4><p style="font-size:6.5px">Lorem ipsum<br>dolor sit amet</p></div>
  <div class="abs item" style="left:296px;top:179px"><h4 style="font-size:8.5px">Lorem Ipsum</h4><p style="font-size:6.5px">Lorem ipsum<br>dolor sit amet</p></div>
</section>

<!-- Break slide -->
<section class="slide break" style="left:35px;top:948px;background:linear-gradient(135deg,#1e4cf2 0%,#2b62ff 50%,#3a7bff 100%);color:var(--white)">
  <div class="abs" role="img" aria-label="Line drawing of a laser processing machine" style="left:53px;top:20px;width:111px;height:190px;background:rgba(255,255,255,.12);border:0.8px solid rgba(255,255,255,.5)"></div>
  <h2 class="abs" style="left:188px;top:86px;font-size:23px;font-weight:600;letter-spacing:-.5px;white-space:nowrap">Break Slide</h2>
  <p class="abs t-sm rule" style="left:190px;top:122px">Lorem ipsum dolor sit amet, consectetur<br>adipiscing elit, sed do eiusmod tempor incididunt<br>ut labore et dolore magna aliqua.</p>
</section>

<!-- Closing slide -->
<section class="slide closing" style="left:434px;top:948px;background:radial-gradient(ellipse at 50% 95%,#1b3fb0 0%,#0b1a5a 40%,#04060f 85%)">
  <div class="abs wordmark" style="left:0;width:390px;top:36px;justify-content:center;font-size:28px">
    <span class="mark" style="width:24px;height:24px"></span>BRENVIK
  </div>
  <p class="abs" style="left:0;width:390px;top:90px;text-align:center;font-family:'Allura',cursive;font-size:44px;color:var(--white)">thank you<span style="color:#3f7bff">!</span></p>
  <p class="abs" style="left:0;width:390px;top:160px;text-align:center;font-size:8.5px;font-weight:400;color:var(--white)">
    <svg width="8" height="9" viewBox="0 0 8 9" style="vertical-align:-1px;margin-right:8px"><path d="M1 0L7 5.5H4.2L5.6 8.6L4.5 9L3.1 6L1 7.8Z" fill="#fff"/></svg>brenvik-systems.example
  </p>
</section>

</body>
</html>
```